Harborview Estates Business Card for Apartment Buildings

Create business cards for resident managers who run apartment buildings. The audience is the public who are searching for apartment rentals, and current residents who live at the apartment building. Key design element will be incorporating the company logo, however, the logo cannot dominate. The building name and manager name are more important than the logo. Current business card design leaves little room for copy, so we may need to reduce the size on the current card to allow for more space for copy.

Target Market(s)

Adults 18-65 years of age, who are looking for an apartment rental, plus current residents who live at our apartment buildings.

Industry/Entity Type

Property Management

Contact Information for Business Card

A major design element will be use of the company logo. Important property and manager contact information must be part of the design. The size of the logo will need to be reduced to make room for building and manager contact copy.

Font styles to use
Sans Serif

Colors
3176b5
000000
959595
ffffff

Requirements
Must have
• 1) Incorporate the company logo.
• 2) Use the company colors (dark blue, black/grey, over white).
• 3) FEATURE THE BUILDING NAME
• 4) FEATURE THE MANAGER NAME
• 5) The company name is less important than BUILDING and MANAGER
• 6) Manager contact information
• **SEE ATTACHED CREATIVE BRIEF**
Nice to have
• 1) Back of card logo watermark
• 2) Ability to write notes on back of carfd
Should not have
• Avoid letting the company logo dominate the card, the building name and manager are more important than the company logo.

```html
<!DOCTYPE html>
<html lang="en">
<head>
<meta charset="utf-8">
<title>Harborview Estates Business Card</title>
<link rel="stylesheet" href="https://fonts.googleapis.com/css2?family=Lato:wght@400;700&display=swap">
<style>
  :root {
    --brand-blue: #1768a8;
    --ink-dark: #2b2b2b;
    --rule-grey: #bdbdbd;
    --paper: #ffffff;
    --backdrop: #ecebe8;
  }
  * { margin: 0; padding: 0; box-sizing: border-box; }
  html, body { width: 1200px; height: 900px; overflow: hidden; }
  body {
    position: relative;
    background: var(--backdrop);
    font-family: "Lato", Arial, sans-serif;
    color: var(--ink-dark);
  }
  .card {
    position: absolute;
    background: var(--paper);
    box-shadow: 0 4px 14px rgba(0,0,0,0.12);
    overflow: hidden;
  }
  /* Front */
  .card-front { left: 77px; top: 33px; width: 590px; height: 365px; }
  .brand-block {
    position: absolute; left: 28px; top: 120px; width: 290px;
    display: flex; align-items: center; gap: 12px;
  }
  .brand-square { width: 34px; height: 34px; background: var(--brand-blue); flex: none; }
  .brand-name {
    font-weight: 700; font-size: 24px; letter-spacing: 0.5px;
    color: var(--brand-blue); text-transform: uppercase; line-height: 1.15;
  }
  .manager { position: absolute; right: 26px; top: 50px; text-align: right; }
  .manager-name { font-weight: 700; font-size: 25px; color: var(--brand-blue); letter-spacing: 0.3px; }
  .manager-title { font-size: 15px; margin-top: 1px; }
  .address {
    position: absolute; right: 28px; top: 162px; text-align: right;
    font-size: 16px; line-height: 21px;
  }
  .contacts {
    position: absolute; right: 26px; top: 242px; list-style: none;
    font-size: 15.5px; line-height: 22px;
  }
  .contacts li { display: flex; justify-content: flex-end; align-items: center; gap: 4px; }
  .contacts svg { width: 13px; height: 13px; fill: var(--brand-blue); flex: none; }
  /* Back */
  .card-back { left: 388px; top: 505px; width: 567px; height: 352px; }
  .back-brand {
    position: absolute; left: 0; right: 0; top: 88px;
    display: flex; justify-content: center; align-items: center; gap: 12px;
  }
  .back-brand .brand-square { width: 30px; height: 30px; }
  .back-brand .brand-name { font-size: 30px; letter-spacing: 1px; }
  .note-lines { position: absolute; left: 50px; right: 50px; top: 190px; }
  .note-line { height: 1.5px; background: var(--rule-grey); margin-bottom: 43px; }
  .card-stripe { position: absolute; left: 0; right: 0; bottom: 0; height: 14px; display: flex; }
  .stripe-blue { flex: 1; background: var(--brand-blue); }
  .stripe-dark { flex: 1; background: var(--ink-dark); }
</style>
</head>
<body>
  <section class="card card-front">
    <div class="brand-block">
      <span class="brand-square"></span>
      <span class="brand-name">Harborview<br>Estates</span>
    </div>
    <div class="manager">
      <h1 class="manager-name">DANIEL WHITFORD</h1>
      <p class="manager-title">Property Manager</p>
    </div>
    <address class="address" style="font-style:normal">
      2750 Linden Ridge<br>Road #B210<br>Oakdale, CA 94361
    </address>
    <ul class="contacts">
      <li>555-214-7730
        <svg viewBox="0 0 16 16" aria-hidden="true"><path d="M2 6c0-2 2-3 6-3s6 1 6 3v1h-3V5.5H5V7H2zM4 8h8l2 5H2z"/></svg>
      </li>
      <li>555-214-7731
        <svg viewBox="0 0 16 16" aria-hidden="true"><path d="M4 1h8v4H4zM1 6h14v6h-3v3H4v-3H1zM5 10v3h6v-3z"/></svg>
      </li>
      <li>dan@harborviewestates.us
        <svg viewBox="0 0 16 16" aria-hidden="true"><path d="M1 3h14v1.5L8 9 1 4.5zM1 6l7 4.5L15 6v7H1z"/></svg>
      </li>
      <li>www.harborviewestates.us
        <svg viewBox="0 0 16 16" aria-hidden="true"><circle cx="8" cy="8" r="7"/><path d="M4 5h3v3H4zM9 9h3v3H9z" fill="#fff"/></svg>
      </li>
    </ul>
  </section>

  <section class="card card-back">
    <div class="back-brand">
      <span class="brand-square"></span>
      <span class="brand-name">Harborview Estates LLC</span>
    </div>
    <div class="note-lines">
      <div class="note-line"></div>
      <div class="note-line"></div>
      <div class="note-line"></div>
    </div>
    <div class="card-stripe">
      <span class="stripe-blue"></span>
      <span class="stripe-dark"></span>
    </div>
  </section>
</body>
</html>
```